Business card design for my company.
I would like the card's background colour to be black. You can also see our web site to get an idea of our brand. https://www.tmwhomecrafting.com.au/
- Name
- Email

```html
<!DOCTYPE html>
<html lang="en">
<head>
<meta charset="utf-8">
<title>TMW Home Crafting – Business Card</title>
<link rel="stylesheet" href="https://fonts.googleapis.com/css2?family=Montserrat:wght@400;500;700&display=swap">
<style>
  :root {
    --stage: #1c1c1c;
    --card-black: #161616;
    --brand-green: #0a9444;
    --back-green: #07964a;
    --back-mark: #0b7a3e;
    --swoosh: #f2f2f2;
    --text-light: #ffffff;
    --radius: 24px;
  }
  * { box-sizing: border-box; margin: 0; padding: 0; }
  html, body {
    width: 1200px;
    height: 1059px;
    overflow: hidden;
    background: var(--stage);
    font-family: "Montserrat", sans-serif;
  }
  .card {
    position: absolute;
    border-radius: var(--radius);
    overflow: hidden;
  }
  .card--front { left: 256px; top: 89px; width: 689px; height: 393px; background: var(--card-black); }
  .card--back { left: 253px; top: 545px; width: 695px; height: 397px; background: var(--back-green); }

  .front-waves { position: absolute; inset: 0; width: 100%; height: 100%; }

  .holder-name {
    position: absolute;
    left: 25px;
    top: 20px;
    font-size: 33px;
    line-height: 1.2;
    font-weight: 700;
    color: var(--brand-green);
  }
  .holder-role {
    position: absolute;
    left: 25px;
    top: 64px;
    font-size: 17px;
    line-height: 1.2;
    font-weight: 400;
    color: var(--text-light);
    letter-spacing: 0.4px;
  }
  .contact-line {
    position: absolute;
    left: 27px;
    display: flex;
    align-items: center;
    gap: 7px;
    font-size: 17.5px;
    line-height: 20px;
    color: var(--text-light);
    letter-spacing: 0.4px;
  }
  .contact-line svg { width: 16px; height: 16px; fill: var(--brand-green); flex: none; }
  .contact-line--location { top: 158px; }
  .contact-line--phone { top: 252px; }
  .contact-line--email { top: 279px; }

  .company-name {
    position: absolute;
    left: 366px;
    top: 84px;
    width: 300px;
    text-align: center;
    font-size: 34px;
    line-height: 1.15;
    font-weight: 700;
    color: var(--text-light);
  }
  .website {
    position: absolute;
    right: 28px;
    top: 345px;
    font-size: 17.5px;
    line-height: 20px;
    color: var(--text-light);
    letter-spacing: 0.3px;
  }

  .back-name {
    position: absolute;
    left: 0;
    top: 0;
    width: 624px;
    height: 397px;
    display: flex;
    align-items: center;
    justify-content: center;
    text-align: center;
    font-size: 52px;
    line-height: 1.15;
    font-weight: 700;
    color: var(--back-mark);
  }
</style>
</head>
<body>
  <section class="card card--front" aria-label="Card front">
    <svg class="front-waves" viewBox="0 0 689 393" preserveAspectRatio="none" aria-hidden="true">
      <path d="M0 346 C90 370 200 372 300 354 C420 332 540 298 689 292 L689 393 L0 393 Z" fill="var(--brand-green)"/>
      <path d="M0 306 C60 330 120 342 200 341 C280 339 360 322 429 310 C360 326 280 350 200 355 C120 359 60 350 0 338 Z" fill="var(--swoosh)"/>
    </svg>

    <h1 class="holder-name">Liam Carverly</h1>
    <p class="holder-role">General Manager</p>

    <p class="contact-line contact-line--location">
      <svg viewBox="0 0 24 24"><path d="M12 2a7 7 0 0 0-7 7c0 5 7 13 7 13s7-8 7-13a7 7 0 0 0-7-7zm0 9.5A2.5 2.5 0 1 1 12 6.5a2.5 2.5 0 0 1 0 5z"/></svg>
      Ferndale Bay, Norvale, Australia
    </p>
    <p class="contact-line contact-line--phone">
      <svg viewBox="0 0 24 24"><path d="M3 9c0-3 4-5 9-5s9 2 9 5v2h-5V9H8v2H3zm4 3h10l3 8H4zm5 2a2.5 2.5 0 1 0 0 5 2.5 2.5 0 0 0 0-5z"/></svg>
      0412 555 718
    </p>
    <p class="contact-line contact-line--email">
      <svg viewBox="0 0 24 24"><path d="M2 6h20v12H2zm2 2v.4l8 5 8-5V8l-8 5z"/></svg>
      info@tmwhomecrafting.com.au
    </p>

    <p class="company-name">TMW<br>Home Crafting</p>

    <p class="website">www.tmwhomecrafting.com.au</p>
  </section>

  <section class="card card--back" aria-label="Card back">
    <p class="back-name">TMW<br>Home Crafting</p>
  </section>
</body>
</html>
```